Ductless Mini Split Business Website

Copper Fern Services is looking to design an eye catching educational website about installing Ductless mini splits.

Similar to this company.
https://www.halvikstream.com/

Coding

Coded - Design and coding required

```html
<!DOCTYPE html>
<html lang="en">
<head>
<meta charset="utf-8">
<title>Copper Fern Services – Ductless System Experts</title>
<link rel="stylesheet" href="https://fonts.googleapis.com/css2?family=Arvo:wght@400;700&family=Montserrat:wght@400;500;600;700&family=Russo+One&display=swap">
<style>
:root{
  --blue:#0b5ec7;
  --blue-dark:#0a4fa8;
  --pink:#f98fb5;
  --navy:#13213f;
  --ink:#1d1d1f;
  --grey:#8a8f98;
  --orange:#e8a23a;
  --yellow:#f2e34a;
  --white:#ffffff;
}
*{box-sizing:border-box;margin:0;padding:0}
html,body{width:1200px;height:4149px;overflow:hidden}
body{position:relative;background:var(--white);font-family:"Montserrat",sans-serif;color:var(--ink)}
.abs{position:absolute}
.btn{position:absolute;display:flex;align-items:center;justify-content:center;background:var(--pink);color:var(--white);font-size:13px;border-radius:20px;letter-spacing:.5px}

/* top bar */
.topbar{left:0;top:0;width:1200px;height:82px;background:var(--blue)}
.topbar .tag{left:430px;top:28px;font-family:"Arvo",serif;font-size:23px;color:var(--white)}
.topbar .call{left:971px;top:36px;font-size:12px;color:#bcd4f5}
.topbar .call b{color:var(--white);font-weight:700}

/* hero */
.hero-photo{left:0;top:82px;width:1200px;height:760px;background:linear-gradient(135deg,#4a4a4e 0%,#6b6560 35%,#3d3f44 65%,#2a2c31 100%)}
.nav{left:0;top:82px;width:1200px;height:68px;background:rgba(120,120,120,.55)}
.brand{display:flex;align-items:center;gap:10px;font-weight:600;color:var(--ink)}
.brand .dot{width:38px;height:38px;border-radius:50%;background:var(--yellow)}
.nav .brand{position:absolute;left:48px;top:15px;font-size:20px}
.nav ul{position:absolute;left:402px;top:26px;display:flex;list-style:none;gap:0}
.nav li{font-size:13px;color:var(--white);font-weight:500}
.hero-title{left:145px;top:272px;font-family:"Arvo",serif;font-weight:700;font-size:72px;line-height:84px;color:var(--white)}
.hero-sub{left:145px;top:456px;font-size:27px;letter-spacing:2.5px;color:#e8e8e8}
.hero-btn{left:143px;top:512px;width:150px;height:36px}

/* intro */
.video{left:101px;top:1004px;width:500px;height:280px;background:linear-gradient(120deg,#5d5a57,#8a8580 50%,#4a4846);box-shadow:0 4px 14px rgba(0,0,0,.2)}
.play{left:337px;top:1126px}
.intro-card{left:677px;top:925px;width:422px;height:440px;background:var(--blue);border-radius:4px;box-shadow:0 6px 18px rgba(0,0,0,.2);color:var(--white)}
.intro-card h2{position:absolute;left:35px;top:60px;font-family:"Arvo",serif;font-weight:700;font-size:26px;line-height:34px}
.intro-card .rule{position:absolute;left:35px;top:130px;width:363px;height:2px;background:var(--orange)}
.intro-card h3{position:absolute;left:35px;top:158px;width:370px;font-size:15px;font-weight:500;letter-spacing:1.4px;line-height:26px}
.intro-card p{position:absolute;left:35px;top:222px;width:360px;font-size:12.6px;line-height:16.7px}
.intro-card .btn{left:35px;top:364px;width:118px;height:32px}

/* services */
.section-title{left:0;width:1200px;text-align:center;font-size:29px;font-weight:500;color:var(--ink)}
.svc{position:absolute;width:237px;height:245px;background:#e8e9eb;border-top:8px solid var(--pink);box-shadow:0 3px 8px rgba(0,0,0,.18);overflow:hidden}
.svc .pic{position:absolute;left:0;top:0;width:100%;height:162px}
.svc .label{position:absolute;left:0;bottom:0;width:100%;height:75px;background:var(--blue);color:var(--white);font-size:15px;font-weight:600;letter-spacing:1.3px;text-align:center;display:flex;align-items:center;justify-content:center;line-height:19px;padding:0 18px}
.k1{background:linear-gradient(180deg,#f1f1f0 0%,#e3e3e1 55%,#8b8780 100%)}
.k2{background:linear-gradient(180deg,#f3f3f3 0%,#cfcfcf 50%,#3b3b3d 100%)}
.k3{background:linear-gradient(180deg,#dcdfe2 0%,#f4f4f4 50%,#b9bcc0 100%)}
.k4{background:linear-gradient(180deg,#3a3634 0%,#6d6762 50%,#c9c6c1 100%)}
.k5{background:linear-gradient(180deg,#e6e0d6 0%,#f5f1ea 50%,#a99f92 100%)}
.k6{background:linear-gradient(180deg,#d8c3a6 0%,#efe4d3 50%,#8b7a66 100%)}
.more{left:514px;top:2162px;width:174px;height:35px;font-size:12px}

/* why */
.why{position:absolute;width:240px}
.why .ring{width:56px;height:56px;border-radius:50%;border:2px solid;display:flex;align-items:center;justify-content:center}
.why .bar{width:56px;height:3px;margin-top:19px}
.why h4{font-size:16px;font-weight:500;margin-top:21px;line-height:19px}
.why p{font-size:11.5px;color:var(--grey);line-height:14.5px;margin-top:8px}

/* testimonial */
.testi{left:0;top:2755px;width:1200px;height:349px;background:linear-gradient(180deg,#6f7378 0%,#8a8e93 45%,#55595f 100%)}
.testi .shade{position:absolute;inset:0;background:rgba(30,32,40,.35)}
.quote{left:0;top:2836px;width:1200px;text-align:center;font-size:40px;font-weight:700;letter-spacing:2.2px;color:var(--white)}
.avatar{left:567px;top:2906px;width:58px;height:58px;border-radius:50%;background:#d6d8db;border:2px solid var(--white)}
.who{left:0;top:2991px;width:1200px;text-align:center;font-family:"Arvo",serif;font-size:14px;color:var(--white)}
.dots{left:551px;top:3053px;display:flex;gap:16px}
.dots span{width:16px;height:16px;border-radius:50%;border:2px solid var(--white)}
.dots span.on{background:var(--white)}

/* support */
.eyebrow{left:0;top:3190px;width:1212px;text-align:center;font-size:16px;letter-spacing:.3px}
.stand{left:0;top:3222px;width:1212px;text-align:center;font-family:"Russo One",sans-serif;font-size:29px;font-style:italic}
.card{position:absolute;top:3328px;width:237px;height:236px;background:var(--white);box-shadow:0 3px 10px rgba(0,0,0,.2)}
.card .pic{height:134px}
.card h5{text-align:center;font-size:15.5px;font-weight:500;margin-top:24px;letter-spacing:.3px}
.card .btn{left:46px;top:187px;width:145px;height:34px;border-radius:0;font-size:14px;font-weight:500}
.p1{background:linear-gradient(135deg,#e9ecef,#b8bec4 60%,#7c8389)}
.p2{background:linear-gradient(135deg,#6a3b22,#c47a45 50%,#3a2114)}
.p3{background:linear-gradient(180deg,#e2d8c6,#f2ebdf 50%,#a98c6c)}

/* footer */
.footer{left:0;top:3702px;width:1200px;height:447px;background:var(--navy);color:var(--white)}
.footer .brand{position:absolute;left:126px;top:143px;font-size:21px;color:var(--white)}
.footer .col{position:absolute;top:150px}
.footer h6{font-size:14.5px;font-weight:500;margin-bottom:14px}
.footer li{list-style:none;font-size:13px;line-height:29px}
</style>
</head>
<body>

<header class="abs topbar">
  <div class="abs tag">Your Ductless System Experts</div>
  <div class="abs call">Call Us Today: <b>999-999-9999</b></div>
</header>

<div class="abs hero-photo" role="img" aria-label="Photo of a smiling group of people gathered around a laptop"></div>
<nav class="abs nav">
  <div class="brand"><span class="dot"></span>Copper Fern</div>
  <ul>
    <li style="margin-right:46px">Home</li>
    <li style="margin-right:46px">About Us</li>
    <li style="margin-right:46px">Ductless Heat Pumps</li>
    <li style="margin-right:46px">FAQ</li>
    <li style="margin-right:46px">Financing</li>
    <li style="margin-right:46px">Reviews</li>
    <li>Contact Us</li>
  </ul>
</nav>
<h1 class="abs hero-title">Ductless<br>Does It Better</h1>
<div class="abs hero-sub">Let Copper Fern Heroes Show You How</div>
<div class="btn hero-btn">Contact Us</div>

<svg class="abs" style="left:0;top:640px" width="1200" height="620" viewBox="0 640 1200 620">
  <path d="M0 780 C80 700 170 650 320 680 C480 710 620 820 800 822 C960 824 1100 760 1200 676 L1200 1260 L0 1260 Z" fill="#fff"/>
  <path d="M0 920 C60 850 150 770 260 778 C420 790 560 890 760 880 C940 872 1100 800 1200 745" fill="none" stroke="#f8c3d4" stroke-width="1.4"/>
  <path d="M0 1195 C60 1120 140 1110 200 1110" fill="none" stroke="#f8c3d4" stroke-width="1.4"/>
  <path d="M600 1130 C640 1140 660 1148 680 1150" fill="none" stroke="#f8c3d4" stroke-width="1.4"/>
  <path d="M1099 1110 C1130 1090 1170 1060 1200 1040" fill="none" stroke="#f8c3d4" stroke-width="1.4"/>
</svg>

<div class="abs video" role="img" aria-label="Video still of a team meeting in front of a wall of sticky notes"></div>
<svg class="abs play" width="36" height="40" viewBox="0 0 36 40"><path d="M2 2 L34 20 L2 38 Z" fill="#fff"/></svg>

<section class="abs intro-card">
  <h2>Copper Fern<br>Ductless Heroes</h2>
  <div class="rule"></div>
  <h3>HELPING PORTLAND AND SURROUNDING AREAS GO DUCTLESS</h3>
  <p>Lorem ipsum dolor sit amet, consectetur adipiscing elit. At auctor at dui mi. Ultricies nulla tellus convallis aliquet augue consequat. Parturient sem molestie tempus ultrices enim vel ut nibh orci. Ac ornare sagittis aliquam tristique pellentesque quam. Interdum volutpat dictumst viverra amet. Vitae in auctor volutpat proin quam pellentesque.</p>
  <div class="btn">Learn More</div>
</section>

<h2 class="abs section-title" style="top:1505px;left:-20px">HOW CAN WE HELP YOU</h2>

<div class="svc" style="left:82px;top:1585px"><div class="pic k1" role="img" aria-label="White kitchen photo"></div><div class="label">BASEBOARD HEAT REPLACEMENT</div></div>
<div class="svc" style="left:348px;top:1585px"><div class="pic k2" role="img" aria-label="Kitchen with pendant lamp photo"></div><div class="label">DUCTLESS FOR ADDITIONAL AND MODELS</div></div>
<div class="svc" style="left:614px;top:1585px"><div class="pic k3" role="img" aria-label="Bright kitchen with chandelier photo"></div><div class="label">DUCTLESS HEAT PUNP FAQ</div></div>
<div class="svc" style="left:880px;top:1585px"><div class="pic k4" role="img" aria-label="Dark cabinet kitchen photo"></div><div class="label">DUCTLESS INSTALLATION</div></div>
<div class="svc" style="left:82px;top:1856px"><div class="pic k5" role="img" aria-label="Kitchen with range hood photo"></div><div class="label">BASEBOARD HEAT REPLACEMENT</div></div>
<div class="svc" style="left:348px;top:1856px"><div class="pic k6" role="img" aria-label="Long wooden kitchen photo"></div><div class="label">DUCTLESS REPAIRS</div></div>
<div class="svc" style="left:614px;top:1856px"><div class="pic k1" role="img" aria-label="White kitchen photo"></div><div class="label">DUCTLESS WARRANTY</div></div>
<div class="svc" style="left:880px;top:1856px"><div class="pic k2" role="img" aria-label="Kitchen with pendant lamp photo"></div><div class="label">WHOLE HOUSE DUCTLESS</div></div>

<div class="btn more">More Ductless Services</div>

<h2 class="abs section-title" style="top:2307px;left:-7px;font-size:30px">Why Shoosing Us</h2>

<div class="why" style="left:158px;top:2397px">
  <div class="ring" style="border-color:#f8c3d4">
    <svg width="28" height="26" viewBox="0 0 28 26"><rect x="1" y="1" width="26" height="24" rx="3" fill="var(--pink)"/><rect x="12" y="8" width="13" height="10" rx="2" fill="#fff"/><circle cx="17" cy="13" r="2" fill="var(--pink)"/></svg>
  </div>
  <div class="bar" style="background:var(--pink)"></div>
  <h4>0% Financing For 60 Mounth</h4>
  <p>Providing options to our customers where it matters most. Offer applies to Norvale systems.</p>
</div>
<div class="why" style="left:477px;top:2449px">
  <div class="ring" style="border-color:var(--yellow)">
    <svg width="30" height="30" viewBox="0 0 30 30"><circle cx="15" cy="15" r="13" fill="none" stroke="var(--yellow)" stroke-width="3"/><path d="M9 15 A6 6 0 0 1 20 12 M21 15 A6 6 0 0 1 10 18" fill="none" stroke="var(--yellow)" stroke-width="2.2"/></svg>
  </div>
  <div class="bar" style="background:var(--yellow)"></div>
  <h4>356 Day Money Back Guarantee</h4>
  <p>Providing options to our customers where it matters most. Offer applies to Norvale systems.</p>
</div>
<div class="why" style="left:802px;top:2400px">
  <div class="ring" style="border-color:var(--blue)">
    <svg width="30" height="30" viewBox="0 0 30 30"><rect x="2" y="2" width="26" height="26" rx="4" fill="var(--blue)"/><circle cx="15" cy="12" r="4.5" fill="#fff"/><path d="M7 24 C8 18 22 18 23 24 Z" fill="#fff"/></svg>
  </div>
  <div class="bar" style="background:var(--blue)"></div>
  <h4>We Are The Experts of<br>Ductless Services</h4>
  <p>Providing options to our customers where it matters most. Offer applies to Norvale systems.</p>
</div>

<section class="abs testi" role="img" aria-label="Photo of a modern white kitchen with a marble island">
  <div class="shade"></div>
</section>
<div class="abs quote">“The Install Is Clean And Looks Great”</div>
<div class="abs avatar" role="img" aria-label="Customer portrait"></div>
<div class="abs who">Marisol T.</div>
<div class="abs dots"><span class="on"></span><span></span><span></span></div>
<svg class="abs" style="left:42px;top:2922px" width="20" height="32" viewBox="0 0 20 32"><path d="M17 3 L4 16 L17 29" fill="none" stroke="#fff" stroke-width="3.5"/></svg>
<svg class="abs" style="left:1124px;top:2922px" width="20" height="32" viewBox="0 0 20 32"><path d="M3 3 L16 16 L3 29" fill="none" stroke="#fff" stroke-width="3.5"/></svg>

<div class="abs eyebrow">SEE OTHER WAYS WE CAN HELP WITH YOUR DUCTLESS SYSTEMS</div>
<h2 class="abs stand">We Stand Behind Our Ductless Services</h2>

<div class="card" style="left:193px"><div class="pic p1" role="img" aria-label="Person working on a laptop"></div><h5>GET SOME ANSWERS</h5><div class="btn">DUCTLESS FAQ</div></div>
<div class="card" style="left:490px"><div class="pic p2" role="img" aria-label="Coins spilling from a jar"></div><h5>TOUR FINANCING OPTION</h5><div class="btn">FINANCING</div></div>
<div class="card" style="left:786px;top:3331px"><div class="pic p3" role="img" aria-label="Bright kitchen with windows"></div><h5>TOUR FINANCING OPTION</h5><div class="btn">OUR BLOG</div></div>

<footer class="abs footer">
  <div class="brand"><span class="dot"></span>Copper Fern</div>
  <div class="col" style="left:759px">
    <h6>QUIK LiNKS</h6>
    <ul><li>Home</li><li>About Us</li><li>Ductless Heat Pumps</li><li>FAQ</li><li>Financing</li><li>Reviews</li><li>Contact Us</li></ul>
  </div>
  <div class="col" style="left:1021px">
    <h6>Follow Us</h6>
    <ul><li>Friendbook</li><li>Snapgram</li><li>Chirper</li><li>Worknet</li><li>999 999 9999</li></ul>
  </div>
</footer>

</body>
</html>
```